Varentoria Business Card and Letter Head

We are a leadership assessment consultancy based in Sydney, Australia. We help executive-level decison-makers select leaders for more senior level roles in corporate and government organisations. Our methodology is based on the latest research from the field of neuroscience.
We need a business card design and matching letter head that presents our company, Varentoria, as a:
1. trusted adviser to senior executive-level decison makers
2. niche consultancy who are experts in the field of assessing leadership talent
3. results-focused solution provider who balance scientific methods with pragmatic solutions
The following company details should be used in all designs:
Company Name: Varentoria
Details (for business card):
Derek Hanford
Prime Capacity Officer
Level 29, Marlow Tower
7 Marlow Square
Sydney, NSW 2000 Australia
Phone: 1300 582 714
Mobile: 0412 637 258
Email: derek.hanford@varentoria-example.com.au
Website: varentoria-example.com.au
I have attached the logo for Varentoria (for both a white and black background) - your business card and letter head designs must incoporate this logo and colour scheme.
Thanks for your interest in this project, I'm looking forward to receiving your ideas.
Regards,
Derek
Target Market(s)
Executive-level decison-makers in corporate and government organisations (e.g., CEO, VP, Head of Human Resources)
Industry/Entity Type
Leadership
Look and feel

```html
<!DOCTYPE html>
<html lang="en">
<head>
<meta charset="utf-8">
<title>Varentoria Business Card</title>
<link rel="stylesheet" href="https://fonts.googleapis.com/css2?family=Source+Sans+3:wght@400;600;700&display=swap">
<style>
  :root {
    --brand-red: #c0301f;
    --ink-dark: #3a3a3c;
    --ink-black: #2a1512;
    --card-white: #ffffff;
    --mark-faint: #ececec;
    --page-bg: #eeeae6;
  }
  * { box-sizing: border-box; margin: 0; padding: 0; }
  html, body { width: 1200px; height: 1094px; overflow: hidden; }
  body {
    background: var(--page-bg);
    font-family: "Source Sans 3", "Myriad Pro", Arial, sans-serif;
    position: relative;
  }
  .card {
    position: absolute;
    left: 220px;
    width: 760px;
    height: 464px;
    border-radius: 26px;
    overflow: hidden;
    box-shadow: 0 2px 6px rgba(0,0,0,0.12);
  }
  .card--front { top: 40px; background: var(--card-white); }
  .card--back { top: 564px; background: var(--brand-red); }

  /* front */
  .side-band {
    position: absolute; left: 0; top: 0; bottom: 0;
    width: 128px; background: var(--brand-red);
  }
  .divider {
    position: absolute; top: 0; bottom: 0; left: 140px;
    width: 4px; background: var(--ink-dark);
  }
  .brand-lockup {
    position: absolute; left: 60px; top: 80px;
    display: flex; align-items: center; gap: 26px;
  }
  .brand-lockup__square {
    width: 104px; height: 104px;
    background: var(--card-white);
    border: 14px solid var(--ink-dark);
  }
  .brand-lockup__name {
    font-size: 64px; font-weight: 700;
    color: var(--ink-dark); letter-spacing: -1px; line-height: 1;
  }
  .address {
    position: absolute; left: 170px; top: 250px;
    color: var(--brand-red); font-size: 20px; line-height: 27px;
  }
  .contact-list {
    position: absolute; left: 170px; top: 338px;
    color: #222; font-size: 20px; line-height: 27px; list-style: none;
  }
  .contact-icons {
    position: absolute; left: 92px; top: 342px;
    list-style: none;
  }
  .contact-icons li { height: 27px; }
  .contact-icons svg { width: 18px; height: 18px; display: block; }
  .faint-square {
    position: absolute; left: 500px; top: 150px;
    width: 190px; height: 190px;
    background: var(--mark-faint);
  }
  .person {
    position: absolute; right: 40px; top: 215px; text-align: right;
  }
  .person__name {
    color: var(--brand-red); font-weight: 700; font-size: 30px; line-height: 1.1;
  }
  .person__title { color: #222; font-size: 20px; margin-top: 2px; }

  /* back */
  .back-lockup {
    position: absolute; left: 90px; top: 160px;
    display: flex; align-items: center; gap: 34px;
  }
  .back-lockup__square {
    width: 130px; height: 130px;
    border: 18px solid var(--ink-black);
  }
  .back-lockup__name {
    font-size: 92px; font-weight: 700; color: var(--ink-black);
    letter-spacing: -1.5px; line-height: 1;
  }
</style>
</head>
<body>

<section class="card card--front" aria-label="Business card front">
  <div class="side-band"></div>
  <div class="divider"></div>

  <div class="brand-lockup">
    <div class="brand-lockup__square"></div>
    <span class="brand-lockup__name">Varentoria</span>
  </div>

  <div class="faint-square"></div>

  <address class="address">
    Level 29, Marlow Tower<br>
    7 Marlow Square<br>
    Sydney, NSW 2000 Australia
  </address>

  <ul class="contact-icons" aria-hidden="true">
    <li><svg viewBox="0 0 18 18"><circle cx="9" cy="9" r="8.5" fill="#fff"/><path d="M6 4.5l2 2-1 1.2c.6 1.3 1.6 2.3 2.9 2.9l1.2-1 2 2-1.2 1.4C8.8 12.7 5.3 9.2 4.6 5.7z" fill="#c0301f"/></svg></li>
    <li><svg viewBox="0 0 18 18"><rect x="5" y="1.5" width="8" height="15" rx="1.5" fill="#fff"/><rect x="6.5" y="3.5" width="5" height="8" fill="#c0301f"/></svg></li>
    <li><svg viewBox="0 0 18 18"><rect x="1" y="4" width="16" height="11" rx="1.5" fill="#fff"/><path d="M1.5 4.8L9 10.5l7.5-5.7" fill="none" stroke="#c0301f" stroke-width="1.3"/></svg></li>
    <li><svg viewBox="0 0 18 18"><circle cx="9" cy="9" r="8" fill="#fff"/><path d="M1 9h16M9 1c-3 3-3 13 0 16M9 1c3 3 3 13 0 16" fill="none" stroke="#c0301f" stroke-width="1.1"/></svg></li>
  </ul>

  <ul class="contact-list">
    <li>1300 582 714</li>
    <li>0412 637 258</li>
    <li>derek.hanford@varentoria-example.com.au</li>
    <li>www.varentoria-example.com.au</li>
  </ul>

  <div class="person">
    <p class="person__name">Derek Hanford</p>
    <p class="person__title">Prime Capacity Officer</p>
  </div>
</section>

<section class="card card--back" aria-label="Business card back">
  <div class="back-lockup">
    <div class="back-lockup__square"></div>
    <span class="back-lockup__name">Varentoria</span>
  </div>
</section>

</body>
</html>
```